Veldmark Supplies Business Card

Professional business card that stand out to our potential customers. Front and back with clean modern design

Industry/Entity Type

Oil and gas

Contact Information for Business Card

Name, address, website , office phone and cell number

Requirements
Must have
• Editable files for each employee

```html
<!DOCTYPE html>
<html lang="en">
<head>
<meta charset="utf-8">
<title>Veldmark Supplies Business Card</title>
<link rel="stylesheet" href="https://fonts.googleapis.com/css2?family=Montserrat:wght@400;500;700;800&display=swap">
<style>
  :root {
    --stage: #e9eaec;
    --card: #ffffff;
    --brand-red: #ea2127;
    --brand-blue: #10b1d3;
    --ink: #1a1a1a;
    --shadow: rgba(0, 0, 0, 0.18);
  }
  * { box-sizing: border-box; margin: 0; padding: 0; }
  html, body {
    width: 1200px;
    height: 874px;
    overflow: hidden;
    background: var(--stage);
    font-family: "Montserrat", sans-serif;
    color: var(--ink);
  }
  .stage {
    width: 1200px;
    height: 874px;
    display: flex;
    flex-direction: column;
    align-items: center;
    justify-content: center;
    gap: 44px;
  }
  .card {
    width: 620px;
    height: 354px;
    background: var(--card);
    border-radius: 26px;
    box-shadow: 0 10px 30px var(--shadow);
    position: relative;
    overflow: hidden;
  }
  .brand {
    display: flex;
    align-items: center;
    gap: 14px;
  }
  .brand-square {
    width: 34px;
    height: 34px;
    background: var(--brand-blue);
    flex: none;
  }
  .brand-name {
    font-weight: 800;
    color: var(--brand-red);
    text-transform: uppercase;
    letter-spacing: 1px;
    line-height: 1;
  }
  .card-front {
    display: flex;
    align-items: center;
    justify-content: center;
  }
  .card-front .brand-name { font-size: 40px; }
  .card-back {
    display: flex;
    align-items: center;
    padding: 0 40px 0 44px;
  }
  .card-back .brand {
    width: 250px;
    flex-direction: column;
    align-items: flex-start;
    gap: 12px;
  }
  .card-back .brand-name { font-size: 30px; }
  .divider {
    width: 2px;
    height: 196px;
    background: var(--brand-red);
    margin: 0 22px 0 18px;
    flex: none;
  }
  .contact-name {
    font-size: 24px;
    font-weight: 700;
    color: var(--brand-red);
  }
  .contact-title {
    font-size: 15px;
    margin-bottom: 12px;
  }
  .contact-list { list-style: none; }
  .contact-list li {
    display: flex;
    align-items: center;
    gap: 8px;
    font-size: 14px;
    line-height: 22px;
  }
  .contact-list svg { width: 13px; height: 13px; fill: var(--brand-blue); flex: none; }
  .address {
    font-size: 14px;
    line-height: 19px;
    margin-top: 8px;
  }
</style>
</head>
<body>
<main class="stage">
  <section class="card card-front" aria-label="Card front">
    <div class="brand">
      <span class="brand-square"></span>
      <span class="brand-name">Veldmark Supplies</span>
    </div>
  </section>

  <section class="card card-back" aria-label="Card back">
    <div class="brand">
      <span class="brand-square"></span>
      <span class="brand-name">Veldmark<br>Supplies</span>
    </div>
    <span class="divider"></span>
    <div class="contact">
      <h1 class="contact-name">Darian Kessler</h1>
      <p class="contact-title">President</p>
      <ul class="contact-list">
        <li><svg viewBox="0 0 16 16"><path d="M2 5c0-2 3-3 6-3s6 1 6 3v1h-3V5H5v1H2zM3 7h10l1 7H2z"/></svg>+1.432.555.0148 x210</li>
        <li><svg viewBox="0 0 16 16"><path d="M4 1l3 4-2 2c1 2 2 3 4 4l2-2 4 3-2 3C7 15 1 9 1 3z"/></svg>+1.432.555.0192</li>
        <li><svg viewBox="0 0 16 16"><path d="M1 3h14v1L8 9 1 4zM1 6l7 5 7-5v7H1z"/></svg>info@veldmarksupplies.com</li>
        <li><svg viewBox="0 0 16 16"><path d="M8 1a7 7 0 100 14A7 7 0 008 1zm0 2c1 1 2 3 2 5s-1 4-2 5c-1-1-2-3-2-5s1-4 2-5zM2.5 7h11v2h-11z"/></svg>www.veldmarksupplies.com</li>
      </ul>
      <p class="address">48 Ridgeway Court<br>Harlow Park, TX 79701 USA</p>
    </div>
  </section>
</main>
</body>
</html>
```